I want a website to be designed for our new company, it's an import and export company for variety of things.

please see the attached Logo for our company and the Images for our different sections for our busienss

Target Market(s)

multiple

Coding

Coded - Design and coding required

Number of Pages Required

5+ page

Font styles to use
Sans Serif

Colors

Designer to choose colors to be used in the design.

Requirements
Must have
• VELTRIS GLOBAL
• KVR globalinks Trading & Contracting provides various services. The Company offers infrastructure construction, oil, enegy and gas services, agricultural projects, real estate development, travel and tourism, and food processing and trading.
• Civil contracting for infrastructure, residential and heavy projects. Through its main subsidiaries; distribution of general food products, construction chemicals including corrosion inhibitors and electrical machinery; provides catering and travel agency services; ownership and operation of a school; offers human sources services including manpower supply.
• Drilling and Gold Mines Used Machinery, All Kinds of Construction Machinery, Drilling Machines are manufactured and sold.
Nice to have
• good designa and beautiful colours, it has too look professional

```html
<!DOCTYPE html>
<html lang="en">
<head>
<meta charset="utf-8">
<title>Veltris Global – Trading &amp; Contracting</title>
<link href="https://fonts.googleapis.com/css2?family=Montserrat:wght@300;400;500;600;700;800&display=swap" rel="stylesheet">
<style>
:root{
  --page:#1b1b1b;
  --header:#111111;
  --footer:#252525;
  --ink:#ffffff;
  --muted:#cfcfcf;
  --accent:#e0891e;
  --purple:#3a2db0;
  --green-top:#4b8a34;
  --green-bot:#1c3a12;
  --red-top:#a82828;
  --red-bot:#5e1010;
  --rule:#3a3a3a;
}
*{box-sizing:border-box;margin:0;padding:0}
html,body{width:1200px;height:4197px;overflow:hidden}
body{background:var(--page);color:var(--ink);font-family:"Montserrat",sans-serif;position:relative}
.abs{position:absolute}
.center{text-align:center}
.accent{color:var(--accent);font-weight:500}

.site-header{left:0;top:0;width:1200px;height:150px;background:var(--header)}
.header-info{display:flex;align-items:center;gap:8px;font-size:16px;line-height:20px}
.header-info b{font-weight:600}
.brand{left:460px;top:22px;width:280px;text-align:center;white-space:nowrap}
.brand-mark{width:34px;height:34px;border-radius:50%;border:2px solid #d8d8d8;margin:0 auto 8px}
.brand-name{font-size:17px;font-weight:500;letter-spacing:2px;color:#e6e6e6}
.main-nav a{position:absolute;top:118px;font-size:17px;color:#e6e6e6;text-decoration:none}
.main-nav a.active{font-weight:700;color:#fff}

.hero{left:0;top:150px;width:1200px;height:650px}
.hero-photo{position:absolute;inset:0 0 30px 0;background:linear-gradient(100deg,#7a5a3a 0%,#a98260 30%,#c9a784 55%,#b08a68 80%,#8a6748 100%)}
.hero-copy{left:636px;top:170px;width:475px}
.hero-copy h1{font-size:36px;font-weight:600;letter-spacing:.5px;margin-bottom:12px;white-space:nowrap}
.hero-copy p{font-size:17px;line-height:31px;color:#f1ece6;text-align:justify}

.btn{display:inline-flex;align-items:center;justify-content:center;gap:10px;height:46px;padding:0 34px;border-radius:23px;font-size:17px;font-weight:700;color:#fff;background:linear-gradient(var(--green-top),var(--green-bot));box-shadow:0 3px 6px rgba(0,0,0,.45)}
.btn.red{background:linear-gradient(var(--red-top),var(--red-bot))}
.btn svg{width:17px;height:17px}

.section-title{font-size:37px;font-weight:300;white-space:nowrap}
.body-copy{font-size:14.5px;line-height:36px;color:#eee;text-align:justify}
.rule{height:1px;background:var(--rule);left:90px;width:1020px}

.about-logo{left:100px;top:1280px;width:440px;height:300px;display:flex;flex-direction:column;align-items:center;justify-content:center;gap:18px}
.about-logo .brand-mark{width:70px;height:70px;margin:0}
.about-logo .brand-name{font-size:32px;letter-spacing:4px;white-space:nowrap}

.service{top:1643px;height:470px;width:600px}
.service.trading{left:0;background:linear-gradient(135deg,#a8565a,#8e3c42 60%,#7e3238)}
.service.contracting{left:600px;background:linear-gradient(135deg,#6a9a5e,#578a4c 60%,#4a7c40)}
.service h2{position:absolute;left:88px;top:62px;font-size:37px;font-weight:300}
.service.contracting h2{left:32px}
.service p{position:absolute;left:88px;top:112px;width:478px;font-size:14.5px;line-height:36px;color:#f4eeee;text-align:justify}
.service.contracting p{left:32px}
.service .btn{position:absolute;left:88px;top:342px;height:54px;width:208px;border-radius:27px}
.service.contracting .btn{left:32px}

.tile{top:2320px;height:437px;display:flex;align-items:flex-end;justify-content:center;padding-bottom:30px;text-align:center;font-size:26px;font-weight:800;line-height:36px}
.tile span{text-shadow:0 2px 6px rgba(0,0,0,.7)}

.blog-slide{top:3055px;height:393px}
.arrow{width:54px;height:54px;border-radius:50%;background:linear-gradient(var(--green-top),var(--green-bot));display:flex;align-items:center;justify-content:center;box-shadow:0 3px 6px rgba(0,0,0,.5)}
.blog-card{left:240px;top:3285px;width:370px;height:196px;background:#1e1e1e;padding:24px 18px 0 16px}
.blog-card h3{font-size:19px;font-weight:700;margin-bottom:10px}
.blog-card p{font-size:11.5px;line-height:27px;color:#ddd;text-align:justify}
.dots{left:923px;top:3468px;display:flex;gap:5px}
.dots i{width:12px;height:12px;border-radius:50%;border:1.5px solid #4b8a34}
.dots i.on{background:#4b8a34}

.site-footer{left:0;top:3540px;width:1200px;height:657px}
.social{left:895px;top:3738px;display:flex;gap:10px}
.social i{width:35px;height:32px;border-radius:3px;background:linear-gradient(var(--green-top),var(--green-bot))}
.contact-col{top:3945px;width:353px;text-align:center}
.contact-col h4{font-size:21px;font-weight:500;margin:16px 0 12px}
.contact-col p{font-size:12.5px;line-height:22px;color:#eee}
.col-rule{top:3925px;width:1px;height:140px;background:#444}
.legal{top:4147px;font-size:12.5px;color:#ddd}
.legal-links{left:623px;top:4147px;display:flex;gap:28px;font-size:12.5px;color:#ddd}
</style>
</head>
<body>

<header class="site-header abs">
  <div class="header-info abs" style="left:195px;top:34px">
    <svg width="40" height="40" viewBox="0 0 40 40"><circle cx="20" cy="20" r="18" fill="none" stroke="#fff" stroke-width="2.5"/><path d="M13 11c2-1 3 0 4 3s-1 3-1 4 4 6 6 6 2-2 4-1 3 2 2 4-4 2-7 0-9-8-10-11 0-4 2-5z" fill="#fff"/></svg>
    <div>Call Us:<br><b>(555) 014 - 2280</b></div>
  </div>
  <div class="brand abs">
    <div class="brand-mark"></div>
    <div class="brand-name">VELTRIS GLOBAL</div>
  </div>
  <div class="header-info abs" style="left:803px;top:34px">
    <svg width="42" height="42" viewBox="0 0 42 42"><circle cx="17" cy="17" r="12" fill="none" stroke="#fff" stroke-width="3"/><path d="M26 26l12 12" stroke="#fff" stroke-width="5" stroke-linecap="round"/></svg>
    <div>Search:<br><b>Enter search here</b></div>
  </div>
  <nav class="main-nav">
    <a class="active" href="#" style="left:141px">HOME</a>
    <a href="#" style="left:229px">About Us</a>
    <a href="#" style="left:339px">Our Services</a>
    <a href="#" style="left:747px">Our Blog</a>
    <a href="#" style="left:856px">Testimonials</a>
    <a href="#" style="left:994px">Contact</a>
  </nav>
</header>

<section class="hero abs">
  <div class="hero-photo" role="img" aria-label="Open-pit mine with a large bucket-wheel excavator under a warm sky"></div>
  <svg class="abs" style="left:0;top:560px" width="1200" height="90" viewBox="0 0 1200 90">
    <path d="M0 60 C40 60 50 40 70 40 C90 40 95 70 140 68 L480 60 C540 58 570 60 600 85 C630 60 660 58 720 60 L1060 68 C1105 70 1110 40 1130 40 C1150 40 1160 60 1200 60 L1200 90 L0 90 Z" fill="var(--page)"/>
    <path d="M0 60 C40 60 50 40 70 40 C90 40 95 70 140 68 L480 60 C540 58 570 60 600 85 C630 60 660 58 720 60 L1060 68 C1105 70 1110 40 1130 40 C1150 40 1160 60 1200 60" fill="none" stroke="var(--purple)" stroke-width="6"/>
  </svg>
  <div class="hero-copy abs">
    <h1>VELTRIS GLOBAL</h1>
    <p>Sed ut perspiciatis unde omnis iste natus error sit voluptatem accusantium doloremque laudantium, totam rem aperiam, sunt explicabo.</p>
    <span class="btn" style="margin-top:16px;height:46px;padding:0 36px">Contact Us
      <svg viewBox="0 0 16 16"><circle cx="8" cy="8" r="8" fill="#fff"/><path d="M4 8h7M8 5l3 3-3 3" stroke="#2b5a1e" stroke-width="2" fill="none"/></svg></span>
  </div>
</section>

<section>
  <h2 class="section-title abs center" style="left:0;top:868px;width:1200px">Welcome to <span class="accent">Veltris Global</span></h2>
  <p class="body-copy abs center" style="left:128px;top:922px;width:944px;text-align:center;font-weight:500">Sed ut perspiciatis unde omnis iste natus error sit voluptatem accusantium doloremque laudantium, totam rem aperiam, eaque ipsa quae ab illo inventore veritatis et quasi architecto beatae vitae dicta sunt explicabo. Nemo enim ipsam voluptatem quia voluptas sit aspernatur aut odit aut fugit, sed quia consequuntur magni dolores eos qui ratione voluptatem sequi nesciunt.</p>
  <div class="abs center" style="left:0;top:1084px;width:1200px"><span class="btn" style="width:192px">Read More
    <svg viewBox="0 0 16 16"><circle cx="8" cy="8" r="8" fill="#fff"/><path d="M4 8h7M8 5l3 3-3 3" stroke="#2b5a1e" stroke-width="2" fill="none"/></svg></span></div>
  <div class="rule abs" style="top:1203px"></div>
</section>

<section>
  <div class="about-logo abs">
    <div class="brand-mark"></div>
    <div class="brand-name">VELTRIS GLOBAL</div>
  </div>
  <h2 class="section-title abs" style="left:565px;top:1268px">About <span class="accent">Veltris Global</span></h2>
  <p class="body-copy abs" style="left:565px;top:1320px;width:545px;font-size:14px">Sed ut perspiciatis unde omnis iste natus error sit voluptatem accusantium doloremque laudantium, totam rem aperiam, eaque ipsa quae ab illo inventore veritatis et quasi architecto beatae vitae dicta sunt explicabo. Nemo enim ipsam voluptatem quia voluptas sit aspernatur aut odit aut fugit nesciunt.</p>
  <span class="btn abs" style="left:565px;top:1516px;width:208px;height:54px;border-radius:27px">Read More
    <svg viewBox="0 0 16 16"><circle cx="8" cy="8" r="8" fill="#fff"/><path d="M4 8h7M8 5l3 3-3 3" stroke="#2b5a1e" stroke-width="2" fill="none"/></svg></span>
</section>

<section>
  <div class="service trading abs" role="img" aria-label="Container port with cargo ships, tinted red">
    <h2>Trading <span class="accent">Services</span></h2>
    <p>Sed ut perspiciatis unde omnis iste natus error sit voluptatem accusantium doloremque laudantium, totam rem aperiam, eaque ipsa quae ab illo inventore veritatis et quasi architecto beatae vitae dicta sunt explicabo. Nemo enim ipsam voluptatem quia voluptas sit aspernatur aut odit aut fugit, sed quia consequuntur magni dolores eos nescunt.</p>
    <span class="btn">Read More
      <svg viewBox="0 0 16 16"><circle cx="8" cy="8" r="8" fill="#fff"/><path d="M4 8h7M8 5l3 3-3 3" stroke="#2b5a1e" stroke-width="2" fill="none"/></svg></span>
  </div>
  <div class="service contracting abs" role="img" aria-label="Contract signing on a desk, tinted green">
    <h2>Contracting <span class="accent">Services</span></h2>
    <p>Sed ut perspiciatis unde omnis iste natus error sit voluptatem accusantium doloremque laudantium, totam rem aperiam, eaque ipsa quae ab illo inventore veritatis et quasi architecto beatae vitae dicta sunt explicabo. Nemo enim ipsam voluptatem quia voluptas sit aspernatur aut odit aut fugit, sed quia consequuntur magni dolores eos nescunt.</p>
    <span class="btn red">Read More
      <svg viewBox="0 0 16 16"><circle cx="8" cy="8" r="8" fill="#fff"/><path d="M4 8h7M8 5l3 3-3 3" stroke="#6a1414" stroke-width="2" fill="none"/></svg></span>
  </div>
</section>

<section>
  <h2 class="section-title abs center" style="left:0;top:2175px;width:1200px">What We <span class="accent">Offer</span></h2>
  <p class="abs center" style="left:160px;top:2230px;width:880px;font-size:17px;line-height:36px;color:#eee">Lorem ipsum dolor sit amet, consectetur adipiscing elit, sed do eiusmod tempor incididunt ut labore et dolore magna aliqua. Quis ipsum suspendisse ultrices gravida.</p>
  <div class="tile abs" style="left:0;width:290px;background:linear-gradient(#8a7250,#6e5a40 60%,#4a3d2c)" role="img" aria-label="Construction site with scaffolding and workers in safety vests"><span>Construction</span></div>
  <div class="tile abs" style="left:302px;width:292px;background:linear-gradient(#8aa6c6,#5c7590 50%,#3a4a5c)" role="img" aria-label="Oil refinery pipes and towers"><span>Oil Industry</span></div>
  <div class="tile abs" style="left:606px;width:291px;background:linear-gradient(#a9c4e0,#c9a85e 55%,#8a6a30)" role="img" aria-label="Combine harvester in a wheat field"><span>Agricultural Projects</span></div>
  <div class="tile abs" style="left:909px;width:291px;background:linear-gradient(#b8d2ea,#d9d9d4 45%,#6e8a58)" role="img" aria-label="Modern apartment buildings"><span>Real Estate<br>Development</span></div>
  <div class="abs center" style="left:0;top:2790px;width:1200px"><span class="btn" style="width:200px">View More
    <svg viewBox="0 0 16 16"><circle cx="8" cy="8" r="8" fill="#fff"/><path d="M4 8h7M8 5l3 3-3 3" stroke="#2b5a1e" stroke-width="2" fill="none"/></svg></span></div>
  <div class="rule abs" style="top:2912px"></div>
</section>

<section>
  <h2 class="section-title abs center" style="left:0;top:2973px;width:1200px">Our Recent <span class="accent">Blog</span></h2>
  <div class="blog-slide abs" style="left:0;width:153px;background:linear-gradient(#5a6876,#7a6050 60%,#5a4a44)" role="img" aria-label="Stacked shipping containers at a port"></div>
  <div class="blog-slide abs" style="left:205px;width:788px;background:linear-gradient(#4d7aa8,#3a6690 50%,#2a4a6a)" role="img" aria-label="Mining excavators working in an open pit at dusk"></div>
  <div class="blog-slide abs" style="left:1045px;width:155px;background:linear-gradient(135deg,#4a5058,#c8c8c8 60%,#e6e6e6)" role="img" aria-label="Business person signing documents"></div>
  <div class="arrow abs" style="left:180px;top:3218px"><svg width="24" height="16" viewBox="0 0 24 16"><path d="M22 8H4M10 2L3 8l7 6" stroke="#fff" stroke-width="3" fill="none"/></svg></div>
  <div class="arrow abs" style="left:967px;top:3218px"><svg width="24" height="16" viewBox="0 0 24 16"><path d="M2 8h18M14 2l7 6-7 6" stroke="#fff" stroke-width="3" fill="none"/></svg></div>
  <article class="blog-card abs">
    <h3>At vero eos et accusamus iusto</h3>
    <p>Sed ut perspiciatis unde omnis iste natus error sit voluptatem accusantium doloremque laudantium, totam rem aperiam, eaque ipsa quae ab illo inventore veritatis et quasi architecto beatae vitae dicta sunt explicabo.</p>
  </article>
  <div class="dots abs"><i></i><i></i><i class="on"></i><i></i></div>
</section>

<footer class="site-footer abs">
  <svg class="abs" style="left:0;top:0" width="1200" height="657" viewBox="0 0 1200 657">
    <path d="M0 70 C30 65 45 90 60 100 C80 70 110 48 170 42 L470 38 C540 36 570 30 600 4 C630 30 660 36 730 38 L1030 42 C1090 48 1120 70 1140 100 C1155 90 1170 65 1200 70 L1200 657 L0 657 Z" fill="var(--footer)"/>
    <path d="M0 70 C30 65 45 90 60 100 C80 70 110 48 170 42 L470 38 C540 36 570 30 600 4 C630 30 660 36 730 38 L1030 42 C1090 48 1120 70 1140 100 C1155 90 1170 65 1200 70" fill="none" stroke="var(--purple)" stroke-width="6"/>
  </svg>
</footer>
<div class="brand abs" style="top:3690px">
  <div class="brand-mark" style="width:46px;height:46px"></div>
  <div class="brand-name" style="font-size:19px">VELTRIS GLOBAL</div>
</div>
<div class="social abs"><i></i><i></i><i></i><i></i><i></i></div>
<h2 class="abs center" style="left:0;top:3850px;width:1200px;font-size:37px;font-weight:500">Contact Information</h2>

<div class="contact-col abs" style="left:70px">
  <svg width="22" height="22" viewBox="0 0 22 22"><path d="M5 2c2-1 3 0 4 3s-1 3-1 4 4 6 6 6 2-2 4-1 3 2 2 4-4 2-7 0S3 10 2 7s1-4 3-5z" fill="var(--accent)"/></svg>
  <h4>CALL US</h4>
  <p>(+155)5 010 2244<br>(+155)5 010 7731</p>
</div>
<div class="col-rule abs" style="left:413px"></div>
<div class="contact-col abs" style="left:424px">
  <svg width="22" height="22" viewBox="0 0 22 22"><path d="M11 2L1 11h3v9h5v-6h4v6h5v-9h3z" fill="var(--accent)"/></svg>
  <h4>FIND US</h4>
  <p>No 18 Harbor Lane 204/6 Portview City,<br>PV, United States</p>
</div>
<div class="col-rule abs" style="left:767px"></div>
<div class="contact-col abs" style="left:780px">
  <svg width="24" height="22" viewBox="0 0 24 22"><rect x="1" y="3" width="22" height="16" rx="2" fill="var(--accent)"/><path d="M2 5l10 7 10-7" stroke="var(--footer)" stroke-width="2" fill="none"/></svg>
  <h4>EMAIL</h4>
  <p>info@veltrisglobal.example<br>support@veltrisglobal.example</p>
</div>

<div class="legal abs" style="left:88px">Veltris Global © 2020. All Rights Reserved.</div>
<div class="legal-links abs"><span>About</span><span>Legal information</span><span>Contact</span><span>Term of service</span><span>Privacy policy</span></div>

</body>
</html>
```